Flyer-Design für Bücherei
Zielgruppe
Wir sind eine ehrenamtlich geführte Bücherei in Kessbach. Wir bieten unseren Kunden eine professionell geführte Bücherei im moderne Stil mit mind. 30 neuen Medien pro Woche. Unsere Zielgruppe sind die Bewohner in Kessbach, vor allen Kinder, Familien mit Kindern und Senioren.
Wir haben über 12.000 Medien, bestehend aus Bilderbücher, Kinderbücher, Jugendliteratur, Romane, Hörbücher für Kinder, Klangis, Reiseführer, Zeitschriften, Spiele und Sachliteratur für Kinder und Jugendliche. Wir haben einen online Katalog und unsere Kunden können online ihre ausgeliehen Medien sehen und verlängern, sowie Vormerkungen platzieren.
Neben den Büchereibetrieb bieten wir Regelmäßige Autorenlesungen, Vorleseaktionen für Kinder, Bastelabende und Führungen für Schul- und Kindergartengruppen.
Ziele des Fördervereins sind:
- Die Bücherei als Kultur-, Bildungs- und Freizeiteinrichtung unterstützen und erhalten
- Durch Öffentlichkeitsarbeit die Bücherei stärker im Bewusstsein der Bevölkerung verankern
- Maßnahmen zur Verbesserung der Leistungsfähigkeit und Attraktivität der Bücherei ergreifen
- Veranstaltung fördern und organisieren
- Neue Freunde und Förderer für die Bücherei gewinnen
Aufgabenstellung
Öffnungszeiten:
Montag, Donnerstag, Freitag 15:00 - 18:00
Kontaktdaten:
Telefon: 07123-58-947
E-Mail: info@lesestube-kessbach.de
Online-Katalog: online.lesestube-kessbach.de
Das Design soll schön und ansprechend sein. Es soll ein zwei mal gefalzter Flyer im Din lang Format sein. Wenn er zusammengefaltet ist soll es eine Startseite geben wo Förderverein der Bücherei Kessbach e.V. drauf steht und auf der Rückseite die Öffnungszeiten und Kontaktdaten.
Bitte formulieren Sie gerne die Texte um, so das die Texte zum Design des Flyers passen . Wir sind eine moderne und aktuelle Bücherei und wollen so auch im Flyer auftreten. Aktuell haben wir nur die Akzentfarbe Rot ansonsten sind wir bei Schwarz und Weiß, wie sie auch im Logo sehen.
Wenn der Flyer uns überzeugt, sind wir gewillt auch noch zwei Roll-Ups designen zu lassen, sowie in Zukunft mit ihnen weiter zusammen zuarbeiten.

```html
<!DOCTYPE html>
<html lang="de">
<head>
<meta charset="utf-8">
<title>Flyer – Förderverein der Bücherei Kessbach e.V.</title>
<link href="https://fonts.googleapis.com/css2?family=Questrial&family=Lobster&display=swap" rel="stylesheet">
<style>
  :root {
    --backdrop: #a8a7a4;
    --paper: #ffffff;
    --accent-red: #e30613;
    --ink: #000000;
    --blush: #fcefea;
    --text-grey: #3c3c3c;
    --photo-dark: #3a2c24;
    --photo-mid: #a8845f;
    --photo-light: #d9c7ad;
  }
  html, body {
    margin: 0;
    padding: 0;
    width: 1200px;
    height: 2709px;
    overflow: hidden;
    background: var(--backdrop);
    font-family: "Questrial", "Century Gothic", sans-serif;
  }
  .spread {
    position: absolute;
    left: 28px;
    top: 805px;
    width: 880px;
    height: 845px;
    transform: scale(1.3);
    transform-origin: 0 0;
  }
  .panel {
    position: absolute;
    top: 0;
    width: 422px;
    height: 845px;
    background: var(--paper);
    overflow: hidden;
  }
  .panel--cover { left: 0; }
  .panel--inside { left: 450px; }

  .cover-photo {
    position: absolute;
    left: 10px;
    top: 13px;
    width: 402px;
    height: 642px;
    background: linear-gradient(120deg, var(--photo-light) 0%, var(--photo-mid) 45%, var(--photo-dark) 100%);
  }
  .brand-box {
    position: absolute;
    background: var(--paper);
    display: flex;
    align-items: center;
    justify-content: center;
    gap: 8px;
  }
  .brand-box--cover { left: 208px; top: 20px; width: 204px; height: 60px; }
  .brand-box--back { left: 220px; top: 767px; width: 184px; height: 55px; }
  .brand-mark {
    width: 14px;
    height: 14px;
    background: var(--accent-red);
  }
  .brand-name {
    font-size: 15px;
    line-height: 1.05;
    color: var(--ink);
    letter-spacing: 0.3px;
  }
  .badge {
    position: absolute;
    top: 558px;
    width: 150px;
    height: 150px;
    border-radius: 50%;
    display: flex;
    flex-direction: column;
    align-items: center;
    justify-content: center;
    color: var(--paper);
    font-family: "Lobster", cursive;
    text-align: center;
  }
  .badge--count { left: 45px; background: var(--accent-red); font-size: 33px; line-height: 1.2; }
  .badge--weekly { left: 217px; background: var(--ink); font-size: 19px; line-height: 1.35; }
  .cover-intro {
    position: absolute;
    left: 19px;
    top: 717px;
    width: 390px;
    margin: 0;
    font-size: 10.5px;
    line-height: 17px;
    color: var(--text-grey);
    letter-spacing: 0.3px;
    word-spacing: 2px;
  }
  .inside-art {
    position: absolute;
    left: 0;
    top: 0;
  }
  .offer-text {
    position: absolute;
    left: 58px;
    top: 115px;
    width: 322px;
    margin: 0;
    font-size: 9.2px;
    line-height: 14.6px;
    color: var(--paper);
    letter-spacing: 0.2px;
    word-spacing: 2px;
  }
  .goals {
    position: absolute;
    left: 58px;
    top: 352px;
    width: 322px;
    font-size: 9.2px;
    line-height: 14.6px;
    color: var(--text-grey);
    letter-spacing: 0.2px;
    word-spacing: 2px;
  }
  .goals p { margin: 0; }
  .goals ul { list-style: none; margin: 0; padding: 0; }
  .goals li::before { content: "\25CF\00a0 "; font-size: 7px; }
  .club-name {
    position: absolute;
    left: 58px;
    top: 620px;
    margin: 0;
    font-size: 15px;
    font-weight: normal;
    color: var(--paper);
    letter-spacing: 0.6px;
    word-spacing: 3px;
  }
  .contact {
    position: absolute;
    left: 58px;
    top: 656px;
    margin: 0;
    font-size: 9.2px;
    line-height: 14.6px;
    color: var(--paper);
    letter-spacing: 0.2px;
    word-spacing: 2px;
  }
  .contact .gap { display: block; height: 14.6px; }
</style>
</head>
<body>
<main class="spread">
  <section class="panel panel--cover">
    <div class="cover-photo" role="img" aria-label="Foto: junges Mädchen liest vor einem Bücherregal in einem aufgeschlagenen blauen Buch"></div>
    <div class="brand-box brand-box--cover">
      <span class="brand-mark"></span>
      <span class="brand-name">LESESTUBE<br>KESSBACH</span>
    </div>
    <div class="badge badge--count"><span>12.000</span><span>Medien</span></div>
    <div class="badge badge--weekly"><span>30</span><span>neuen Medien</span><span>pro Woche</span></div>
    <p class="cover-intro">Wir sind eine ehrenamtlich geführte Bücherei in Kessbach.<br>Wir bieten unseren Kunden eine professionell geführte Bücherei im moderne Stil mit mind. 30 neuen Medien pro Woche. Unsere Zielgruppe sind die Bewohner in Kessbach, vor allen Kinder, Familien mit Kindern und Senioren.</p>
  </section>

  <section class="panel panel--inside">
    <svg class="inside-art" width="422" height="845" viewBox="0 0 422 845" aria-hidden="true">
      <rect x="14" y="263" width="394" height="570" fill="var(--blush)"/>
      <polygon points="14,109 212,24 408,109 408,347 212,263 14,347" fill="var(--accent-red)"/>
      <polygon points="14,590 212,504 408,590 408,833 14,833" fill="var(--ink)"/>
    </svg>
    <p class="offer-text">Wir haben über 12.000 Medien, bestehend aus Bilderbücher, Kinderbücher, Jugendliteratur, Romane, Hörbücher für Kinder, Klangis, Reiseführer, Zeitschriften, Spiele und Sachliteratur für Kinder und Jugendliche. Wir haben einen online Katalog und unsere Kunden können online ihre ausgeliehen Medien sehen und verlängern, sowie Vormerkungen platzieren.<br>Neben den Büchereibetrieb bieten wir Regelmäßige Autorenlesungen, Vorleseaktionen für Kinder, Bastelabende und Führungen für Schul- und Kindergartengruppen.</p>
    <div class="goals">
      <p>Ziele des Fördervereins sind:</p>
      <ul>
        <li>Die Bücherei als Kultur-, Bildungs- und Freizeiteinrichtung unterstützen und erhalten</li>
        <li>Durch Öffentlichkeitsarbeit die Bücherei stärker im Bewusstsein der Bevölkerung verankern</li>
        <li>Maßnahmen zur Verbesserung der Leistungsfähigkeit und Attraktivität der Bücherei ergreifen</li>
        <li>Veranstaltung fördern und organisieren</li>
        <li>Neue Freunde und Förderer für die Bücherei gewinnen</li>
      </ul>
    </div>
    <h1 class="club-name">Förderverein der Bücherei Kessbach e.V.</h1>
    <p class="contact">Öffnungszeiten:<br>Montag, Donnerstag, Freitag 15:00 – 18:00<span class="gap"></span>Kontaktdaten:<br>Telefon: 07123-58-947<br>E-Mail: info@lesestube-kessbach.de<br>Online-Katalog: online.lesestube-kessbach.de</p>
    <div class="brand-box brand-box--back">
      <span class="brand-mark"></span>
      <span class="brand-name">LESESTUBE<br>KESSBACH</span>
    </div>
  </section>
</main>
</body>
</html>
```